Brand New Product Needs Sales Focused Website Design

Looking for design of Homepage, Category Page & Product Page for single product sales focused website. TrundleCrate manufacture and distribute a brand new product to the market called PalTote-Case which is a super strong, re-useable, folding & stacking plastic box which can be seen on our current website www.paltote-case.example PalTote-Case was originally developed as an alternative to supermarket carrier bags and was pitched as a box for life against the other low end re-useable products. The original version was made from recycled plastic and pitched very much as environmental product. We are now taking a different direction and have re-designed the boxes in 5 bright and fashionable designs and although we still want the primary focus to be supermarket shopping we want to position the product as a design led, must have shopping and household accessory rather than a boring, cheap looking black plastic box. The new designs will still have the environmental benefits of being able to be re-used thousands of times and being 100% recyclable and save on the imminent 5p tax on carrier bags in the UK however the new designs will not be made from recycled material. Although the main use for PalTote-Case is supermarket shopping it has a multitude of other uses especially where you need temporary storage - laundry, back of the car, moving house/students, gardening, days out, home office filing (will take A4 file), recycling and much more - PalTote-Case is made out of super strong Polypropylene and can be easily washed and sanitised after use and can be folded and unfolded thousands of times and so will last for many years. PalTote-Case is a product that needs to be seen in action to be understood so the web design must quickly and easily communicate what PalTote-Case is and how it works - this can be done with video, images and copy. Our current website does not work for many reasons:- it is too busy, has too much information, tries too hard and ultimately isn't working. Any of the images off our current website can be supplied for use. Once the concept of the website is agreed I can get these photoshopped with the new designs. Pictures of new designs for reference will be attached to this brief. Ultimately we want the website to convert visitors to sales and therefore designers with a proven track record in this field are especially welcome to enter. We also have a Dropbox folder with over 100 product and situation images in - please send email address and we will send an invite to the folder. Due to Christmas period this competition will be run over 15 days however we may choose to extend the deadline to account for the non working days. Any questions feel free to ask - we will respond within 24 hours where possible.

```html
<!DOCTYPE html>
<html lang="en">
<head>
<meta charset="utf-8">
<title>PalTote-Case – Box For Life</title>
<link href="https://fonts.googleapis.com/css2?family=Raleway:wght@400;500;600;700&family=Open+Sans:wght@400;600;700&display=swap" rel="stylesheet">
<style>
:root{
  --orange:#e07b0c;
  --orange-soft:#ea9a3e;
  --cream:#f3ede1;
  --leaf:#9cc43a;
  --top-green:#35a06e;
  --black:#000;
  --ink:#333;
  --price:#d0161a;
  --strike:#3a7fb0;
  --footer:#474747;
  --footer-base:#2d2d2d;
  --footer-text:#cfcfcf;
  --rule:#d9d9d9;
  --white:#fff;
}
*{box-sizing:border-box;margin:0;padding:0}
html,body{width:913px;height:1200px;overflow:hidden;background:var(--white)}
body{position:relative;font-family:"Open Sans",sans-serif;color:var(--ink)}
.abs{position:absolute}
.top-strip{left:0;top:0;width:913px;height:5px;background:var(--orange)}
.account-links{right:84px;top:16px;font-size:8.5px;color:var(--ink);word-spacing:1px}
.account-links span{margin:0 3px}
.brand{left:85px;top:26px}
.brand-name{font-family:"Raleway",sans-serif;font-weight:700;font-size:42px;color:var(--orange);letter-spacing:-.5px;line-height:1}
.brand-tag{font-family:"Raleway",sans-serif;font-weight:500;font-size:15px;color:var(--black);margin:18px 0 0 26px;letter-spacing:.3px}
.call-icon{left:592px;top:50px;width:34px;height:34px;background:var(--orange);border-radius:3px;display:flex;align-items:center;justify-content:center}
.call-divider{left:636px;top:48px;height:38px;border-left:1px dashed var(--orange)}
.call-text{left:649px;top:44px;font-family:"Raleway",sans-serif}
.call-text .label{font-weight:700;font-size:19px;color:var(--ink)}
.call-text .number{font-weight:500;font-size:24px;color:var(--orange);letter-spacing:1.5px;margin-top:-2px}
.main-nav{left:83px;top:123px;width:747px;height:44px;background:var(--black);display:flex}
.main-nav a{display:flex;align-items:center;justify-content:center;color:var(--white);font-size:11px;text-decoration:none;border-right:1px solid #444;height:100%}
.main-nav a.active{background:var(--orange)}
.hero{left:83px;top:179px;width:747px;height:329px;background:var(--orange);overflow:hidden}
.hero-photo{position:absolute;left:276px;top:0;width:471px;height:329px;
  background:linear-gradient(100deg,rgba(224,123,12,0) 0%,var(--cream) 12%,#eef0d8 40%,var(--orange-soft) 56%,#d98a5c 66%,var(--top-green) 82%,#2b8c5f 100%)}
.hero-title{position:absolute;left:19px;top:30px;font-family:"Raleway",sans-serif;font-weight:500;font-size:57px;line-height:58px;color:var(--white)}
.hero-copy{position:absolute;left:20px;top:158px;width:270px;font-family:"Raleway",sans-serif;font-size:14px;line-height:23px;color:var(--white)}
.shop-now{position:absolute;left:20px;top:251px;width:123px;height:44px;background:var(--black);color:var(--white);border-radius:3px;font-family:"Raleway",sans-serif;font-weight:500;font-size:16px;display:flex;align-items:center;justify-content:center}
.design-band{left:83px;top:520px;width:747px;height:51px;background:var(--black);display:flex;align-items:center;justify-content:center}
.design-band::before,.design-band::after{content:"";position:absolute;left:4px;right:4px;border-top:1.5px dashed var(--white)}
.design-band::before{top:5px}.design-band::after{bottom:5px}
.design-band p{font-family:"Raleway",sans-serif;font-size:24px;color:var(--white)}
.design-band b{font-weight:700}
.categories{left:85px;top:585px;width:164px;height:191px;border:1px solid var(--rule)}
.panel-head{height:30px;background:var(--orange);color:var(--white);font-family:"Raleway",sans-serif;font-weight:600;font-size:16px;padding:3px 10px;border-bottom:3px solid var(--white);box-shadow:0 1px 0 var(--rule)}
.categories ul{list-style:none;padding:5px 4px 0 4px}
.categories li{height:25.7px;font-size:10px;color:var(--black);display:flex;align-items:center;border-bottom:1px dashed var(--rule)}
.categories li:last-child{border-bottom:none}
.categories li::before{content:"➤";font-size:8px;margin:0 12px 0 5px}
.signup{left:85px;top:784px;width:164px;height:148px;background:repeating-linear-gradient(90deg,#e01f1f 0 3px,#cf1717 3px 6px);border:1px solid #b51010;color:var(--white);text-align:center}
.signup .pre{font-family:"Raleway",sans-serif;font-weight:600;font-size:13px;margin-top:8px}
.signup .pre small{font-size:11px}
.signup .big{font-family:"Raleway",sans-serif;font-weight:600;font-size:26px;line-height:26px}
.signup .field{margin:6px auto 0;width:143px;height:22px;background:var(--white);color:#222;font-size:10px;text-align:left;padding:4px 6px}
.signup .send{position:absolute;right:10px;bottom:8px;width:65px;height:22px;background:#111;border-radius:4px;font-size:13px;display:flex;align-items:center;justify-content:center}
.featured{left:270px;top:585px;width:558px;height:266px;border:1px solid var(--rule)}
.featured .panel-head{height:44px;display:flex;align-items:center;font-size:17px;padding:0 13px;text-transform:uppercase}
.featured .panel-head .view-all{margin-left:auto;font-family:"Open Sans",sans-serif;font-size:10px;text-decoration:underline;text-transform:none}
.product{position:absolute;top:57px;width:171px}
.product-shot{height:119px;border:1px solid var(--rule);
  background:radial-gradient(ellipse 62% 40% at 45% 58%,#f4f7ec 0%,#e3eec6 55%,var(--leaf) 78%,rgba(156,196,58,0) 80%),var(--white)}
.product h3{font-weight:600;font-size:10.5px;line-height:13px;color:var(--ink);margin:7px 0 0 5px}
.product .was{font-size:9.5px;color:var(--strike);text-decoration:line-through;margin:5px 0 0 5px}
.product .row{display:flex;align-items:center;justify-content:space-between;margin:5px 4px 0 5px}
.product .now{font-weight:700;font-size:12px;color:var(--price)}
.product .cart{width:71px;height:18px;background:var(--orange);color:var(--white);font-size:8.5px;font-weight:700;display:flex;align-items:center;justify-content:center}
.awards{left:270px;top:860px;width:558px;height:72px;border:1px solid var(--rule)}
.awards-label{position:absolute;left:0;top:0}
.awards-label span{position:absolute;left:19px;top:18px;font-family:"Raleway",sans-serif;font-weight:700;font-size:24px;color:var(--white)}
.award-badge{position:absolute;top:22px;height:26px;background:#cfcfcf;border-radius:3px}
.site-footer{left:0;top:961px;width:913px;height:203px;background:var(--footer);color:var(--footer-text)}
.foot-col{position:absolute;top:34px}
.foot-col h4{font-family:"Raleway",sans-serif;font-weight:400;font-size:15px;color:var(--white);margin-bottom:20px}
.foot-col p.about{font-size:8px;line-height:9px;width:180px}
.foot-col ul{list-style:none;font-size:8.5px;line-height:13.7px}
.contact-line{font-size:9.5px;margin-top:8px;display:flex}
.contact-line b{font-weight:400;width:45px}
.contact-line span{color:var(--white)}
.contact-line a{color:var(--orange);text-decoration:none}
.foot-news p{font-size:8.5px;line-height:9px;width:165px}
.foot-news .form{display:flex;margin-top:16px}
.foot-news .input{width:137px;height:23px;background:var(--white);color:#999;font-size:8.5px;padding:6px 15px}
.foot-news .go{width:53px;height:23px;background:var(--orange);color:var(--white);font-size:9px;display:flex;align-items:center;justify-content:center}
.cards{display:flex;gap:8px;margin-top:34px}
.cards i{display:block;width:28px;height:17px;background:#e6e6e6;border-radius:2px}
.footer-base{left:0;top:1164px;width:913px;height:36px;background:var(--footer-base);color:var(--white);font-size:10px;display:flex;align-items:center;padding:0 83px}
.footer-base .legal{margin-left:auto}
</style>
</head>
<body>
<div class="abs top-strip"></div>
<nav class="abs account-links">My Account <span>|</span> My Wishlist <span>|</span> My Cart <span>|</span> Checkout <span>|</span> Log In</nav>

<header class="abs brand">
  <div class="brand-name">PalTote-Case</div>
  <div class="brand-tag">INGENENIOUS &amp; PRACTICAL</div>
</header>

<div class="abs call-icon">
  <svg width="20" height="20" viewBox="0 0 24 24"><path fill="#fff" d="M6.6 10.8a15.1 15.1 0 0 0 6.6 6.6l2.2-2.2c.3-.3.7-.4 1-.2 1.1.4 2.3.6 3.6.6.6 0 1 .4 1 1V20c0 .6-.4 1-1 1A17 17 0 0 1 3 4c0-.6.4-1 1-1h3.5c.6 0 1 .4 1 1 0 1.3.2 2.5.6 3.6.1.3 0 .7-.2 1z"/></svg>
</div>
<div class="abs call-divider"></div>
<div class="abs call-text">
  <div class="label">Feel Free To Call Us</div>
  <div class="number">123 456 78901</div>
</div>

<nav class="abs main-nav">
  <a class="active" style="width:96px">HOME</a>
  <a style="width:128px">CATAGORY</a>
  <a style="width:137px">OUR RANGE</a>
  <a style="width:120px">GAURANTEE</a>
  <a style="width:132px">PRODUCTS</a>
  <a style="width:134px;border-right:none">CONTACT US</a>
</nav>

<section class="abs hero">
  <div class="hero-photo" role="img" aria-label="Product photo: a smiling shopper in a green top holds up the white PalTote-Case folding box printed with pink, orange and green flowers, its side marked www.paltote-case.example"></div>
  <h1 class="hero-title">BOX<br>FOR LIFE</h1>
  <p class="hero-copy">Lorem ipsum dolor sit amet, consectetur adipiscing elit. In quis enim est. Quisque lobortis commodo</p>
  <div class="shop-now">SHOP NOW</div>
</section>

<div class="abs design-band"><p>Now Available In <b>5</b> BRIGHT &amp; FASHIONABLE designs</p></div>

<aside class="abs categories">
  <div class="panel-head">Categories</div>
  <ul>
    <li>FURNITURE</li><li>ELECTRONICS</li><li>APPAREL</li><li>MUSIC</li><li>EBOOKS</li><li>CARE &amp; BEAUTY PRODUCTS</li>
  </ul>
</aside>

<aside class="abs signup">
  <div class="pre">Sign Up <small>For</small> our</div>
  <div class="big">NewsLetter</div>
  <div class="field">Name...</div>
  <div class="field" style="margin-top:10px">E-Mail....</div>
  <div class="send">Submit</div>
</aside>

<section class="abs featured">
  <div class="panel-head">
    <svg width="30" height="30" viewBox="0 0 24 24" style="margin-right:10px"><path fill="#f6a04a" stroke="#fff" stroke-width=".8" d="M12 1.5l3.1 6.6 7.2.9-5.3 5 1.4 7.1L12 17.6 5.6 21.1 7 14 1.7 9l7.2-.9z"/></svg>
    Featured Products
    <span class="view-all">View All</span>
  </div>
  <article class="product" style="left:12px">
    <div class="product-shot" role="img" aria-label="Product photo: open PalTote-Case folding box with white, pink and green floral print and an orange buy tag"></div>
    <h3>Lorem Ipsum Dolor Sit Amet Consectutuer</h3>
    <div class="was">Don't Pay $12.32</div>
    <div class="row"><span class="now">Today $3.99</span><span class="cart">Add to Cart</span></div>
  </article>
  <article class="product" style="left:196px">
    <div class="product-shot" role="img" aria-label="Product photo: open PalTote-Case folding box with white, pink and green floral print and an orange buy tag"></div>
    <h3>Lorem Ipsum Dolor Sit Amet Consectutuer</h3>
    <div class="was">Don't Pay $30.02</div>
    <div class="row"><span class="now">Today $9.98</span><span class="cart">Add to Cart</span></div>
  </article>
  <article class="product" style="left:376px">
    <div class="product-shot" role="img" aria-label="Product photo: open PalTote-Case folding box with white, pink and green floral print and an orange buy tag"></div>
    <h3>Lorem Ipsum Dolor Sit Amet Consectutuer</h3>
    <div class="was">Don't Pay $12.32</div>
    <div class="row"><span class="now">Today $2.29</span><span class="cart">Add to Cart</span></div>
  </article>
</section>

<section class="abs awards">
  <svg class="awards-label" width="136" height="72" viewBox="0 0 136 72"><polygon points="0,0 110,0 135,36 110,72 0,72" fill="var(--orange)"/></svg>
  <div class="awards-label"><span>Awards</span></div>
  <div class="award-badge" style="left:145px;width:98px"></div>
  <div class="award-badge" style="left:264px;width:52px"></div>
  <div class="award-badge" style="left:340px;width:120px"></div>
  <div class="award-badge" style="left:488px;width:62px"></div>
</section>

<footer class="abs site-footer">
  <div class="foot-col" style="left:83px;top:38px">
    <h4 style="margin-bottom:10px">About Us</h4>
    <p class="about">Lorem ipsum dolor sit amet, consectetuer adipiscing elit. Aenean commodo ligula eget dolor. Aenean massa. Cum sociis natoque penatibus et magnis dis parturient montes, nascetur ridiculus mus. Donec quam felis, ultricies nec, pellentesque eu, pretium quis, sem.</p>
    <div class="contact-line" style="margin-top:10px"><b>Phone:</b><span>1-123-456-789-01</span></div>
    <div class="contact-line"><b>e-mail:</b><a>info@trundlecrate.example</a></div>
  </div>
  <div class="foot-col" style="left:331px">
    <h4>Lorem Ipsum</h4>
    <ul><li>Lorem ipsum</li><li>Dolor sit</li><li>Amet</li><li>Consectutuer</li><li>Adipicsing</li></ul>
  </div>
  <div class="foot-col" style="left:495px">
    <h4>Our Support</h4>
    <ul style="margin-left:5px"><li>Site Map</li><li>Search Terms</li><li>Advanced Search</li><li>Mobile</li><li>Contact Us</li><li>Mobile</li><li>Addresses</li></ul>
  </div>
  <div class="foot-col foot-news" style="left:637px">
    <h4 style="margin:0 0 8px 2px">Newsletter</h4>
    <p>Join thousands of other people subscribe to our news</p>
    <div class="form"><div class="input">INSERT EMAIL</div><div class="go">SUBMIT</div></div>
    <div class="cards"><i></i><i></i><i></i><i></i><i></i><i></i></div>
  </div>
</footer>
<div class="abs footer-base"><span>© 2014 PalTote-Case All Rights Reserved</span><span class="legal">Privacy Policy &nbsp;|&nbsp; Terms &amp; Conditions</span></div>
</body>
</html>
```